Create a business promotion flyer to leave in customer mailboxes. We are a bulk petroleum supplier, servicing any industry that requires diesel. Base in griffith NSW, servicing griffith area and surrounds.

Business Name - Terra Diesel
Fuel@terradiesel-example.com.au
Owen - 0491 570 362 ohartley@terradiesel-example.com.au
Liam - 0491 570 718 lprosser@terradiesel-example.com.au
Simon - 0491 570 905 skenway@terradiesel-example.com.au
Office 02 5550 1734

Bulk Fuel deliveries.
Oils & lubricants
Local Family owned business

```html
<!DOCTYPE html>
<html lang="en">
<head>
<meta charset="utf-8">
<title>Terra Diesel – Your Local Bulk Fuel Supplier</title>
<link rel="stylesheet" href="https://fonts.googleapis.com/css2?family=Roboto+Condensed:wght@700;800&family=Quicksand:wght@500;600&display=swap">
<style>
  :root {
    --red: #e8291c;
    --grey: #666666;
    --grey-light: #ececec;
    --charcoal: #2a2a2a;
    --ink: #111111;
    --white: #ffffff;
    --sky-top: #4f7fc0;
    --sky-low: #c9d6e6;
    --ground: #bdbdbd;
  }
  * { box-sizing: border-box; margin: 0; padding: 0; }
  html, body { width: 927px; height: 1200px; overflow: hidden; background: var(--white); }
  .flyer {
    position: relative; width: 927px; height: 1200px; overflow: hidden;
    font-family: "Quicksand", sans-serif; color: var(--ink); background: var(--white);
  }
  .hero { position: absolute; left: 0; top: 0; width: 927px; height: 760px; }
  .brand {
    position: absolute; top: 58px; left: 0; width: 100%;
    display: flex; justify-content: center; align-items: center; gap: 12px;
    font-family: "Quicksand", sans-serif; font-weight: 600; font-size: 44px; line-height: 1;
    color: var(--red); letter-spacing: .5px;
  }
  .brand-dot { width: 18px; height: 18px; border-radius: 50%; background: var(--grey); }

  .headline {
    position: absolute; top: 596px; left: 0; width: 100%; text-align: center;
    font-family: "Roboto Condensed", sans-serif; font-weight: 800; line-height: 1;
  }
  .headline-top { font-size: 52px; color: var(--ink); }
  .headline-main { font-size: 52px; color: var(--red); margin-top: 0; }
  .tagline {
    position: absolute; top: 698px; left: 0; width: 100%; text-align: center;
    font-size: 18px; font-weight: 500; color: var(--grey);
  }

  .services { position: absolute; left: 40px; top: 747px; width: 440px; }
  .service { position: absolute; left: 0; display: flex; }
  .service-badge {
    width: 88px; height: 88px; border-radius: 50%; border: 1.5px solid var(--red);
    display: flex; align-items: center; justify-content: center; flex-shrink: 0;
  }
  .service-badge span {
    width: 72px; height: 72px; border-radius: 50%; background: var(--grey);
    display: flex; align-items: center; justify-content: center;
  }
  .service-text { margin-left: 13px; }
  .service-title {
    font-family: "Roboto Condensed", sans-serif; font-weight: 700; font-size: 26px;
    color: var(--grey); line-height: 1.25; text-transform: uppercase;
  }
  .service-title em { font-style: normal; color: var(--red); }
  .service-body { font-size: 15.5px; line-height: 22px; margin-top: 6px; color: var(--ink); }

  .contact {
    position: absolute; left: 494px; top: 748px; width: 433px; height: 375px;
  }
  .contact-bg { position: absolute; inset: 0; }
  .contact-title {
    position: absolute; left: 103px; top: 30px;
    font-family: "Roboto Condensed", sans-serif; font-weight: 700; font-size: 28px; color: var(--white);
  }
  .contact-rule { position: absolute; left: 104px; top: 67px; width: 60px; height: 2px; background: var(--red); }
  .person { position: absolute; left: 100px; width: 300px; display: flex; align-items: center; }
  .person-icon {
    width: 37px; height: 37px; border-radius: 50%; background: var(--red);
    display: flex; align-items: center; justify-content: center; flex-shrink: 0;
  }
  .person-info { margin-left: 6px; color: var(--white); font-size: 11px; line-height: 13px; font-weight: 500; white-space: nowrap; }
  .person-name { font-family: "Roboto Condensed", sans-serif; font-weight: 700; font-size: 15px; line-height: 18px; text-transform: uppercase; }
  .contact-divider { position: absolute; left: 104px; width: 211px; height: 1px; background: #9a9a9a; }

  .footer { position: absolute; left: 0; top: 1123px; width: 927px; height: 77px; }
  .footer-links {
    position: absolute; left: 70px; top: 20px; display: flex; align-items: center; gap: 10px;
    font-family: "Roboto Condensed", sans-serif; font-weight: 700; font-size: 17px; color: var(--white);
  }
  .footer-globe {
    width: 36px; height: 36px; border-radius: 50%; background: var(--white);
    display: flex; align-items: center; justify-content: center;
  }
  .footer-slogan {
    position: absolute; left: 669px; top: 24px;
    font-family: "Roboto Condensed", sans-serif; font-weight: 800; font-size: 22px; color: var(--white);
  }
</style>
</head>
<body>
<main class="flyer">

  <svg class="hero" viewBox="0 0 927 760">
    <defs>
      <linearGradient id="skyFade" x1="0" y1="0" x2="0" y2="1">
        <stop offset="0" stop-color="var(--sky-top)"/>
        <stop offset="0.55" stop-color="var(--sky-low)"/>
        <stop offset="0.56" stop-color="#d8dce0"/>
        <stop offset="1" stop-color="var(--ground)"/>
      </linearGradient>
    </defs>
    <rect x="0" y="0" width="927" height="640" fill="url(#skyFade)" role="img"
          aria-label="Photo of a white fuel tanker road train parked in front of a steel depot shed under a blue sky"/>
    <path d="M0 90 Q463 294 927 71 V0 H0 Z" fill="var(--red)"/>
    <path d="M0 62 Q463 268 927 30 V0 H0 Z" fill="var(--grey)"/>
    <path d="M0 55 Q463 268 927 -10 V0 H0 Z" fill="var(--white)"/>

    <path d="M0 600 C250 450 650 430 927 590 V760 H0 Z" fill="var(--red)"/>
    <path d="M0 690 C250 500 650 470 927 600 V760 H0 Z" fill="var(--grey)"/>
    <path d="M0 730 C280 520 650 490 927 640 V760 H0 Z" fill="var(--grey-light)"/>
    <path d="M0 746 C300 540 650 510 927 690 V760 H0 Z" fill="var(--white)"/>
  </svg>

  <div class="brand"><span class="brand-dot"></span>Terra Diesel</div>

  <h1 class="headline">
    <div class="headline-top">YOUR LOCAL</div>
    <div class="headline-main">BULK FUEL SUPPLIER</div>
  </h1>
  <p class="tagline">Reliable Diesel Delivery Across Griffith &amp; Surrounding Areas</p>

  <section class="services">
    <article class="service" style="top:0">
      <div class="service-badge"><span>
        <svg width="38" height="38" viewBox="0 0 38 38" fill="none" stroke="#fff" stroke-width="2">
          <rect x="8" y="10" width="20" height="16" rx="3"/>
          <path d="M4 26 H34"/><circle cx="11" cy="30" r="2.5"/><circle cx="26" cy="30" r="2.5"/>
          <path d="M18 13 c-3 4 -3 6 0 7 c3 -1 3 -3 0 -7z" fill="#fff"/>
        </svg></span></div>
      <div class="service-text">
        <h2 class="service-title">Bulk Fuel <em>Deliveries</em></h2>
        <p class="service-body">Reliable supply of quality diesel for<br>any industry.</p>
      </div>
    </article>

    <article class="service" style="top:115px">
      <div class="service-badge"><span>
        <svg width="38" height="38" viewBox="0 0 38 38" fill="#fff">
          <path d="M11 6 c-5 7 -5 11 0 12 c5 -1 5 -5 0 -12z"/>
          <circle cx="21" cy="24" r="8"/><circle cx="21" cy="24" r="3" fill="var(--grey)"/>
          <rect x="19.5" y="13" width="3" height="22"/><rect x="10" y="22.5" width="22" height="3"/>
          <rect x="28" y="10" width="6" height="1.6"/><rect x="29" y="14" width="5" height="1.6"/>
        </svg></span></div>
      <div class="service-text">
        <h2 class="service-title">Oils &amp; <em>Lubricants</em></h2>
        <p class="service-body">Premium oils and lubricants to keep your<br>equipment performing at its best.</p>
      </div>
    </article>

    <article class="service" style="top:236px">
      <div class="service-badge"><span>
        <svg width="38" height="38" viewBox="0 0 38 38" fill="none" stroke="#fff" stroke-width="2">
          <path d="M6 14 H26 L24 9 H8 Z"/><rect x="8" y="14" width="16" height="16"/>
          <rect x="11" y="20" width="5" height="4"/><path d="M19 30 V20 H22 V30"/>
          <path d="M30 5 a5 5 0 0 1 5 5 c0 4 -5 9 -5 9 s-5 -5 -5 -9 a5 5 0 0 1 5 -5z"/>
        </svg></span></div>
      <div class="service-text">
        <h2 class="service-title">Local Family-Owned<br><em>Business</em></h2>
        <p class="service-body">Committed to outstanding service<br>and long-term customer relationships.</p>
      </div>
    </article>
  </section>

  <section class="contact">
    <svg class="contact-bg" viewBox="0 0 433 375" preserveAspectRatio="none" aria-hidden="true">
      <path d="M72 0 H433 V375 H72 L0 185 Z" fill="var(--charcoal)"/>
    </svg>
    <h2 class="contact-title">CONTACT US</h2>
    <div class="contact-rule"></div>

    <div class="person" style="top:88px">
      <div class="person-icon"><svg width="18" height="18" viewBox="0 0 18 18" fill="#fff"><circle cx="9" cy="5" r="4"/><path d="M1 17 a8 7 0 0 1 16 0z"/></svg></div>
      <div class="person-info"><div class="person-name">Owen</div>0491 570 362<br>ohartley@terradiesel-example.com.au</div>
    </div>
    <div class="contact-divider" style="top:144px"></div>

    <div class="person" style="top:158px">
      <div class="person-icon"><svg width="18" height="18" viewBox="0 0 18 18" fill="#fff"><circle cx="9" cy="5" r="4"/><path d="M1 17 a8 7 0 0 1 16 0z"/></svg></div>
      <div class="person-info"><div class="person-name">Liam</div>0491 570 718<br>lprosser@terradiesel-example.com.au</div>
    </div>
    <div class="contact-divider" style="top:214px"></div>

    <div class="person" style="top:232px">
      <div class="person-icon"><svg width="18" height="18" viewBox="0 0 18 18" fill="#fff"><circle cx="9" cy="5" r="4"/><path d="M1 17 a8 7 0 0 1 16 0z"/></svg></div>
      <div class="person-info"><div class="person-name">Simon</div>0491 570 905<br>skenway@terradiesel-example.com.au</div>
    </div>
    <div class="contact-divider" style="top:289px"></div>

    <div class="person" style="top:306px">
      <div class="person-icon"><svg width="18" height="18" viewBox="0 0 24 24" fill="#fff"><path d="M6.6 10.8a15 15 0 0 0 6.6 6.6l2.2-2.2a1 1 0 0 1 1-.25 11 11 0 0 0 3.6.6 1 1 0 0 1 1 1V20a1 1 0 0 1-1 1A17 17 0 0 1 3 4a1 1 0 0 1 1-1h3.5a1 1 0 0 1 1 1 11 11 0 0 0 .6 3.6 1 1 0 0 1-.25 1z"/></svg></div>
      <div class="person-info"><div class="person-name">Office</div>02 5550 1734</div>
    </div>
  </section>

  <footer class="footer">
    <svg width="927" height="77" viewBox="0 0 927 77" aria-hidden="true" style="position:absolute;inset:0">
      <rect width="927" height="77" fill="var(--grey)"/>
      <path d="M641 0 H927 V77 H590 Z" fill="var(--white)"/>
      <path d="M651 0 H927 V77 H600 Z" fill="var(--red)"/>
    </svg>
    <div class="footer-links">
      <span class="footer-globe"><svg width="24" height="24" viewBox="0 0 24 24" fill="none" stroke="var(--grey)" stroke-width="1.6"><circle cx="12" cy="12" r="10"/><ellipse cx="12" cy="12" rx="4.5" ry="10"/><path d="M2 12H22M4 6.5H20M4 17.5H20"/></svg></span>
      <span>Fuel@terradiesel-example.com.au</span><span>|</span><span>www.terradiesel-example.com.au</span>
    </div>
    <div class="footer-slogan">FUELING YOUR SUCCESS</div>
  </footer>

</main>
</body>
</html>
```